Redesign of the UI of a customer service platform

To improve the user experience of our customers, we need a new design for our agent interface of our customer service platform (velorant.com).
The focus will be on the dashboard and the inbox screens (see attached) along with the common UI elements (Buttons, menu, fonts, forms...)
We want a simple and distinctive design

Target Market(s)

Worldwide

Industry/Entity Type

It Service

Number of Pages Required

3 page

Font styles to use
Sans Serif

Requirements
Must have
• New Onboarding page: this is a new page that is shown to user the first time they login to the platform. This will replace the current onboarding screen (setup SMS, Setup widget...etc)
• Dashboard page: to access important information and activate services (see screenshot from current site)
• Inbox page: to manage all the interactions with customers. (see screenshot from current site)
• UI elements (buttons, menus, forms, tables, fonts, color palette)

```html
<!DOCTYPE html>
<html lang="en">
<head>
<meta charset="utf-8">
<title>velorant — Inbox</title>
<link rel="stylesheet" href="https://fonts.googleapis.com/css2?family=Ubuntu:wght@400;500&display=swap">
<style>
:root{
  --ink:#1b1b1b;
  --sidebar:#262626;
  --sidebar-line:#3a3a3a;
  --topbar:#000;
  --red:#d81d1d;
  --coral:#ec6a6a;
  --green:#b9dc8c;
  --sky:#8dcfdf;
  --teal:#8bc8b4;
  --sand:#d4c486;
  --slate:#5a8e99;
  --cyan:#6cc6d3;
  --page:#edf0ee;
  --line:#cfd3d1;
  --pink-line:#f0a9ae;
  --muted:#666;
}
*{box-sizing:border-box;margin:0;padding:0}
html,body{width:1200px;height:1002px;overflow:hidden}
body{font-family:"Ubuntu",sans-serif;background:var(--page);color:var(--ink);position:relative}
.abs{position:absolute}
.topbar{left:0;top:0;width:1200px;height:50px;background:var(--topbar)}
.brand{left:0;top:0;width:129px;height:50px;display:flex;align-items:center;justify-content:center;gap:5px;color:#fff;font-size:14px;font-weight:500}
.brand .dot{width:10px;height:10px;border-radius:50%;background:#fff}
.sidebar{left:0;top:50px;width:129px;height:952px;background:var(--sidebar)}
.nav-item{position:absolute;left:0;width:129px;display:flex;align-items:center;color:#fff;font-size:11px;border-bottom:1px solid var(--sidebar-line)}
.nav-item svg{position:absolute;left:23px}
.nav-item span{position:absolute;left:54px}
.nav-item.active{background:var(--red);border-bottom:none}
.main{left:138px;top:61px;width:1027px;height:862px;border:1px solid var(--line);background:var(--page)}
.main-head{left:138px;top:61px;width:1027px;height:53px;border-bottom:1px solid var(--line)}
.title{left:164px;top:77px;font-size:19px}
.card{background:#fff;border:1px solid var(--line)}
.tab{position:absolute;display:flex;align-items:center;justify-content:center;color:#fff;font-size:11px}
.search{left:190px;top:214px;width:413px;height:38px;border:1px solid var(--pink-line);background:#fff}
.search span{position:absolute;left:68px;top:12px;font-size:11px;color:#555}
.row{position:absolute;left:188px;width:415px;height:85px}
.avatar{position:absolute;border-radius:50%}
.row .avatar{left:11px;top:10px;width:68px;height:68px}
.row .name{position:absolute;left:100px;top:22px;font-size:14.5px}
.row .snip{position:absolute;left:102px;top:46px;font-size:11.5px}
.row .when{position:absolute;right:18px;top:23px;font-size:11.5px;color:var(--coral)}
.btn{position:absolute;display:flex;align-items:center;justify-content:center;color:#fff;font-size:8.5px}
.bubble{position:absolute;border:1px solid var(--pink-line);background:#fff;color:var(--red);font-size:11px}
.stamp{position:absolute;font-size:10.5px;color:#333}
.field{position:absolute;font-size:8.5px;color:#444}
</style>
</head>
<body>
<div class="abs topbar"></div>
<div class="abs brand"><span class="dot"></span>velorant</div>

<svg class="abs" style="left:982px;top:13px" width="120" height="26" viewBox="0 0 120 26">
  <path d="M4 18h16l-2-3v-5a6 6 0 0 0-12 0v5z M10 20a2 2 0 0 0 4 0" fill="none" stroke="#fff" stroke-width="1.4"/>
  <circle cx="16" cy="6" r="5" fill="#e21c1c"/><text x="16" y="9" font-size="7" fill="#fff" text-anchor="middle" font-family="Ubuntu,sans-serif">2</text>
  <path d="M53 9h14a4 4 0 0 1 4 4v2a4 4 0 0 1-4 4h-8l-5 4v-4a4 4 0 0 1-5-4v-2a4 4 0 0 1 4-4z" fill="none" stroke="#fff" stroke-width="1.4"/>
  <circle cx="69" cy="6" r="5" fill="#3bbf3b"/><text x="69" y="9" font-size="7" fill="#fff" text-anchor="middle" font-family="Ubuntu,sans-serif">4</text>
</svg>
<div class="abs avatar" role="img" aria-label="Agent profile photo" style="left:1088px;top:8px;width:30px;height:30px;background:radial-gradient(circle at 50% 40%,#d9b9a2,#6a5448 70%,#fff 72%)"></div>
<svg class="abs" style="left:1144px;top:13px" width="22" height="24" viewBox="0 0 22 24">
  <path d="M12 4H2v17h10M9 12h12M17 8l4 4-4 4" fill="none" stroke="#fff" stroke-width="1.4"/>
</svg>

<nav class="abs sidebar">
  <div class="nav-item" style="top:0;height:44px"><svg width="22" height="16" viewBox="0 0 22 16"><path d="M2 14a9 9 0 1 1 18 0M11 14l-4-5" fill="none" stroke="#fff" stroke-width="1.3"/></svg><span>Dashboard</span></div>
  <div class="nav-item active" style="top:44px;height:56px"><svg width="20" height="18" viewBox="0 0 20 18"><path d="M2 9h5l1 3h4l1-3h5v8H2zM10 1v8M7 6l3 3 3-3" fill="none" stroke="#fff" stroke-width="1.4"/></svg><span>Inbox</span></div>
  <div class="nav-item" style="top:100px;height:52px"><svg width="22" height="22" viewBox="0 0 22 22"><path d="M3 14 14 3l5 5L8 19z M7 10l5 5" fill="none" stroke="#fff" stroke-width="1.3"/></svg><span>Tickets</span></div>
  <div class="nav-item" style="top:152px;height:52px"><svg width="20" height="22" viewBox="0 0 20 22"><circle cx="10" cy="7" r="5" fill="none" stroke="#fff" stroke-width="1.3"/><path d="M2 21c0-5 4-7 8-7s8 2 8 7z" fill="none" stroke="#fff" stroke-width="1.3"/></svg><span>Clients</span></div>
  <div class="nav-item" style="top:204px;height:48px"><svg width="18" height="22" viewBox="0 0 18 22"><rect x="2" y="1" width="14" height="20" fill="none" stroke="#fff" stroke-width="1.3"/><path d="M5 7h8M5 11h8M5 15h8" stroke="#fff" stroke-width="1"/></svg><span>Report</span></div>
  <div class="nav-item" style="top:252px;height:43px"><svg width="26" height="20" viewBox="0 0 26 20"><circle cx="8" cy="13" r="4" fill="none" stroke="#fff" stroke-width="3" stroke-dasharray="2 1.6"/><circle cx="19" cy="7" r="3" fill="none" stroke="#fff" stroke-width="2.5" stroke-dasharray="1.6 1.3"/></svg><span style="top:11px">Setting</span></div>
</nav>

<div class="abs main"></div>
<div class="abs main-head"></div>
<h1 class="abs title" style="font-weight:400">Inbox</h1>

<section class="abs card" style="left:174px;top:142px;width:449px;height:570px"></section>
<div class="tab" style="left:191px;top:158px;width:87px;height:28px;background:#ee3e3e;justify-content:space-between;padding:0 14px;font-size:11.5px"><span>Agent</span><span>2</span></div>
<div class="tab" style="left:282px;top:158px;width:87px;height:28px;background:var(--green)">Department</div>
<div class="tab" style="left:373px;top:158px;width:87px;height:28px;background:var(--sky)">Account</div>
<div class="abs search">
  <svg style="position:absolute;left:19px;top:11px" width="18" height="18" viewBox="0 0 18 18"><circle cx="7" cy="7" r="5.5" fill="none" stroke="#e02020" stroke-width="1.6"/><path d="M11 11l5 5" stroke="#e02020" stroke-width="1.8"/></svg>
  <span>Search</span>
</div>

<div class="row" style="top:265px;background:#f0eeee">
  <div class="avatar" role="img" aria-label="Client portrait" style="background:radial-gradient(circle,#d7b3a0,#5a3a34)"></div>
  <div class="name">Mara Quell</div><div class="when">2 days ago</div><div class="snip">Lorem ipsum dolor sit amet, consectetuer</div>
</div>
<div class="row" style="top:355px;background:#fbfaf0">
  <div class="avatar" role="img" aria-label="Client portrait" style="background:radial-gradient(circle,#dcbca6,#f6f3ef);border:1px solid var(--pink-line)"></div>
  <div class="name">Mara Quell</div><div class="when">2 days ago</div><div class="snip">Lorem ipsum dolor sit amet, consectetuer</div>
</div>
<div class="row" style="top:446px;background:#fdecec">
  <div class="avatar" role="img" aria-label="Client portrait" style="background:radial-gradient(circle,#d7b3a0,#5a3a34)"></div>
  <div class="name">Mara Quell</div><div class="when">2 days ago</div><div class="snip">Lorem ipsum dolor sit amet, consectetuer</div>
</div>
<div class="row" style="top:537px;background:#f9ebeb">
  <div class="avatar" role="img" aria-label="Client portrait" style="background:radial-gradient(circle,#dcbca6,#f6f3ef);border:1px solid var(--pink-line)"></div>
  <div class="name">Mara Quell</div><div class="when">2 days ago</div><div class="snip">Lorem ipsum dolor sit amet, consectetuer</div>
</div>

<div class="abs" style="left:218px;top:766px;width:200px;text-align:center;font-size:11.5px">Done</div>
<div class="abs" style="left:218px;top:786px;width:200px;text-align:center;font-size:8px;color:var(--muted)">No Done clients</div>

<section class="abs card" style="left:671px;top:142px;width:449px;height:570px"></section>
<div class="abs" style="left:700px;top:153px;font-size:11.5px">Dana Holloway</div>
<div class="btn" style="left:922px;top:153px;width:58px;height:18px;background:var(--coral)">Close</div>
<div class="btn" style="left:988px;top:153px;width:57px;height:18px;background:var(--teal)">Transfer</div>
<div class="btn" style="left:1052px;top:153px;width:58px;height:18px;background:var(--sand)">Ban</div>
<div class="abs" style="left:672px;top:187px;width:447px;height:10px;background:#e4e4e4;font-size:5px;line-height:10px">
  <span style="position:absolute;left:17px">More Details</span><span style="position:absolute;right:24px">Save transcript</span>
</div>

<div class="stamp" style="left:1064px;top:224px">2 min</div>
<div class="avatar abs" role="img" aria-label="Client portrait" style="left:714px;top:232px;width:77px;height:77px;background:radial-gradient(circle,#d7b3a0,#4e322d)"></div>
<div class="bubble" style="left:813px;top:240px;width:284px;height:63px"><span style="position:absolute;left:28px;top:16px">hru?</span></div>
<svg class="abs" style="left:799px;top:251px" width="16" height="14" viewBox="0 0 16 14"><path d="M15 1 1 7l14 6" fill="#fff" stroke="#f0a9ae"/></svg>

<div class="stamp" style="left:725px;top:343px">0 min</div>
<div class="bubble" style="left:718px;top:359px;width:284px;height:63px"><span style="position:absolute;right:32px;top:15px">hru?</span></div>
<svg class="abs" style="left:1000px;top:393px" width="16" height="14" viewBox="0 0 16 14"><path d="M1 1l14 6-14 6" fill="#fff" stroke="#f0a9ae"/></svg>
<div class="avatar abs" role="img" aria-label="Agent portrait" style="left:1027px;top:351px;width:77px;height:77px;background:radial-gradient(circle,#dcbca6,#f6f3ef);border:1px solid #e6e6e6"></div>

<div class="abs" style="left:686px;top:646px;width:412px;height:46px;border:1px solid #999;background:#fff;font-size:8px;color:#555;padding:19px 0 0 17px">Type a message here...</div>

<section class="abs card" style="left:671px;top:728px;width:447px;height:178px"></section>
<div class="btn" style="left:679px;top:736px;width:57px;height:21px;background:var(--coral)">Details</div>
<div class="btn" style="left:745px;top:736px;width:57px;height:21px;background:var(--cyan)">Tickets</div>
<div class="btn" style="left:810px;top:736px;width:57px;height:21px;background:var(--slate)">History</div>
<div class="btn" style="left:1062px;top:734px;width:50px;height:19px;background:#e83030;gap:5px"><svg width="8" height="8" viewBox="0 0 8 8"><path d="M1 7l1-3 4-3 1 1-3 4z" fill="none" stroke="#fff" stroke-width=".9"/></svg>Edit</div>

<svg class="abs" style="left:688px;top:782px" width="14" height="72" viewBox="0 0 14 72">
  <text x="2" y="11" font-size="11" font-weight="500" fill="#333" font-family="Ubuntu,sans-serif">A</text>
  <rect x="1" y="32" width="11" height="8" fill="none" stroke="#555"/><path d="M1 32l5.5 5 5.5-5" fill="none" stroke="#555"/>
  <path d="M2 58c0 6 4 10 10 10l1-2-3-2-1 1c-2-1-3-2-4-4l1-1-2-3z" fill="#444"/>
</svg>
<div class="field" style="left:708px;top:784px">Name</div>
<div class="field" style="left:708px;top:813px">Email</div>
<div class="field" style="left:709px;top:843px">Phone</div>

<svg class="abs" style="left:891px;top:781px" width="16" height="74" viewBox="0 0 16 74">
  <path d="M8 13s-4-4-4-7a4 4 0 0 1 8 0c0 3-4 7-4 7z" fill="none" stroke="#555"/><circle cx="8" cy="6" r="1.3" fill="#555"/>
  <path d="M2 42l3-5 8-7-2 8-5 4zM2 42l2-4" fill="#666"/>
  <circle cx="8" cy="66" r="5.5" fill="none" stroke="#555"/><path d="M2.5 66h11M8 60.5c-3 3-3 8 0 11M8 60.5c3 3 3 8 0 11" fill="none" stroke="#555" stroke-width=".8"/>
</svg>
<div class="field" style="left:917px;top:784px">Address</div>
<div class="field" style="left:916px;top:813px">City/ Town</div>
<div class="field" style="left:919px;top:843px">Country</div>
</body>
</html>
```